Existing Website Requiring new Pages

I have an existing word press website that was built using elementor.
Website: www.tallowcrestcare.com.au
I require the Vacancies page (https://www.tallowcrestcare.com.au/vacancies/) to be modified to display our new properties along with minor tweaks to how the information is presented.
The vacancies to be displayed are the exactly the same as those that are located on the homepage of QMR website (https://qmr.org.au/)
The new pages that link off the Vacancies tab will require custom design.
There are roughly 8 pages/properties to be incorporated. i wish for the design to be very similar to that displayed in the following link; https://www.polunda.com.au/vacancies/merrylands
Along with this the back end has not been updated for the last 3 years so it also requires some maintenance.
Website is in the disability industry and the custom pages will display information relative to Property Vacancies.
I have attached a ZIP file with some design guides, the information for each of the properties (which will need to be modified to show our business name Tallowcrest Care) and the example of how it is to look based off the Polunda website.
If you guys have any suggestions or ideas on how to make this more presentable or possible i'm open to your ideas.
Target Market(s)
People looking for SDA properties custom built for people with a disability
Industry/Entity Type
Disability
Coding
Coded - Design and coding required
Number of Pages Required
5+ page

```html
<!DOCTYPE html>
<html lang="en">
<head>
<meta charset="utf-8">
<title>Vacancies – Tallowcrest Care</title>
<link href="https://fonts.googleapis.com/css2?family=Montserrat:wght@400;500;600;700&display=swap" rel="stylesheet">
<style>
:root{
  --teal:#1fd0b6;
  --teal-text:#1cc4a8;
  --ink:#2b2b2b;
  --nav:#3a3a3a;
  --accent:#f08a52;
  --muted:#8a8a8a;
  --footer-bg:#f7f7f7;
  --bar:#1b1b1b;
  --line:#e3e3e3;
  --blue:#1e6fb5;
}
*{box-sizing:border-box;margin:0;padding:0}
html,body{width:1200px;height:2207px;overflow:hidden}
body{position:relative;font-family:'Montserrat',sans-serif;background:#fff;color:var(--ink)}
.top-rule{position:absolute;left:0;top:0;width:1200px;height:2px;background:#333}
.site-header{position:absolute;left:0;top:2px;width:1200px;height:123px;background:#fff}
.brand{position:absolute;left:130px;top:44px;display:flex;align-items:center;gap:8px}
.brand-dot{width:14px;height:14px;border-radius:50%;background:var(--teal)}
.brand-name{font-size:17px;font-weight:600;color:var(--teal-text);letter-spacing:.5px}
.main-nav{position:absolute;top:57px;left:574px;display:flex;gap:0}
.main-nav a{position:absolute;white-space:nowrap;font-size:10.5px;font-weight:700;letter-spacing:.6px;color:var(--nav);text-decoration:none}
.main-nav a.active{color:var(--accent)}
.hero{position:absolute;left:0;top:125px;width:1200px;height:514px;overflow:hidden;background:linear-gradient(120deg,#c9dff3 0%,#d9a48f 35%,#8d6a5e 55%,#e9c98a 100%)}
.hero svg{position:absolute;left:0;top:0}
.hero-title{position:absolute;left:722px;top:84px;font-size:60px;font-weight:600;color:#fff;letter-spacing:1px}
.card{position:absolute;width:309px;height:325px}
.card-photo{position:absolute;left:0;top:0;width:309px;height:230px}
.card-edge{position:absolute;top:217px;width:11px;height:13px;background:var(--teal)}
.card-edge.left{left:0;clip-path:polygon(0 40%,100% 0,100% 100%,0 100%)}
.card-edge.right{right:0;clip-path:polygon(0 40%,100% 0,100% 60%,0 100%)}
.card-label{position:absolute;left:11px;top:195px;width:284px;height:130px;background:#fff;box-shadow:0 2px 6px rgba(0,0,0,.12);text-align:center}
.card-town{margin-top:33px;font-size:22px;font-weight:500;color:var(--teal-text);letter-spacing:.5px;white-space:nowrap}
.card-type{margin-top:12px;font-size:19px;font-weight:500;color:var(--ink);letter-spacing:.3px}
.site-footer{position:absolute;left:0;top:1870px;width:1200px;height:270px;background:var(--footer-bg)}
.footer-brand{position:absolute;left:139px;top:88px;display:flex;align-items:center;gap:8px}
.contact-list{position:absolute;left:135px;top:189px;list-style:none}
.contact-list li{display:flex;align-items:center;gap:7px;font-size:11.5px;color:var(--muted);height:21px}
.contact-list svg{flex:none}
.social{position:absolute;left:522px;top:51px;display:flex;flex-direction:column;gap:8px}
.social span{display:block;width:31px;height:31px;border-radius:50%;background:var(--blue)}
.social span.badge{background:#7b2f8c}
.social span.dark{background:#1f1f1f}
.footer-col{position:absolute;top:42px;width:215px}
.footer-col h3{font-size:13px;font-weight:500;color:var(--ink);border-left:2px solid var(--teal);padding-left:12px;letter-spacing:.4px;line-height:13px;margin-bottom:12px}
.footer-col ul{list-style:none;border-top:1px solid var(--line)}
.footer-col li{font-size:11.5px;color:var(--muted);line-height:20px;padding:5px 0;border-bottom:1px solid var(--line)}
.bottom-bar{position:absolute;left:0;top:2140px;width:1200px;height:67px;background:var(--bar);text-align:center;font-size:11.5px;color:#d0d0d0;line-height:67px}
.to-top{position:absolute;right:12px;top:16px;width:30px;height:30px;background:#111;display:flex;align-items:center;justify-content:center}
</style>
</head>
<body>
<div class="top-rule"></div>
<header class="site-header">
  <div class="brand"><span class="brand-dot"></span><span class="brand-name">Tallowcrest Care</span></div>
  <nav class="main-nav">
    <a style="left:0">HOME</a>
    <a style="left:59px">ABOUT US</a>
    <a class="active" style="left:142px">WHAT WE DO ⌄</a>
    <a style="left:261px">REFERRALS</a>
    <a style="left:352px">FEEDBACK</a>
    <a style="left:438px">CONTACT US</a>
  </nav>
</header>

<section class="hero" role="img" aria-label="Smiling group of friends with a woman in a wheelchair on a teal diagonal band">
  <svg width="1200" height="514"><polygon points="776,0 1200,0 891,514 411,514" fill="#1fd4b8" opacity=".92"/></svg>
  <h1 class="hero-title">VACANCIES</h1>
</section>

<main>
  <article class="card" style="left:111px;top:729px">
    <div class="card-photo" role="img" aria-label="Penrith house exterior" style="background:linear-gradient(180deg,#e8eef5 0%,#b7bcc2 50%,#5e7a48 100%)"></div>
    <span class="card-edge left"></span><span class="card-edge right"></span>
    <div class="card-label"><p class="card-town">PENRITH</p><p class="card-type">4 BEDROOM SIL HOME</p></div>
  </article>
  <article class="card" style="left:446px;top:729px">
    <div class="card-photo" role="img" aria-label="Mount Druitt brick house" style="background:linear-gradient(180deg,#a9cfee 0%,#a4684c 45%,#4f8a35 75%,#8fb85a 100%)"></div>
    <span class="card-edge left"></span><span class="card-edge right"></span>
    <div class="card-label"><p class="card-town">MOUNT DRUITT</p><p class="card-type">4 BEDROOM SIL HOME</p></div>
  </article>
  <article class="card" style="left:779px;top:729px">
    <div class="card-photo" role="img" aria-label="Casula house" style="background:linear-gradient(180deg,#8ccaf5 0%,#bfe2fb 40%,#e6d9b0 70%,#4a7c3a 100%)"></div>
    <span class="card-edge left"></span><span class="card-edge right"></span>
    <div class="card-label"><p class="card-town">CASULA</p><p class="card-type">4 BEDROOM SIL HOME</p></div>
  </article>

  <article class="card" style="left:111px;top:1085px">
    <div class="card-photo" role="img" aria-label="Eastwood heritage house" style="background:linear-gradient(180deg,#d9e6f2 0%,#d8c9ad 45%,#8a7a66 80%,#4f6a3a 100%)"></div>
    <span class="card-edge left"></span><span class="card-edge right"></span>
    <div class="card-label"><p class="card-town">EASTWOOD</p><p class="card-type">4 BEDROOM SIL HOME</p></div>
  </article>
  <article class="card" style="left:446px;top:1085px">
    <div class="card-photo" role="img" aria-label="Baulkham Hills house with palm" style="background:linear-gradient(180deg,#9fd0f4 0%,#cbe6f8 40%,#d3b99a 65%,#4e8a3c 100%)"></div>
    <span class="card-edge left"></span><span class="card-edge right"></span>
    <div class="card-label"><p class="card-town">BAULKHAM HILLS</p><p class="card-type">4 BEDROOM SIL HOME</p></div>
  </article>
  <article class="card" style="left:779px;top:1085px">
    <div class="card-photo" role="img" aria-label="Merrylands brick house" style="background:linear-gradient(180deg,#8ec7f1 0%,#cfe6f6 40%,#c2623a 65%,#6aab3d 100%)"></div>
    <span class="card-edge left"></span><span class="card-edge right"></span>
    <div class="card-label"><p class="card-town">MERRYLANDS</p><p class="card-type">4 BEDROOM SIL HOME</p></div>
  </article>

  <article class="card" style="left:279px;top:1450px">
    <div class="card-photo" role="img" aria-label="Sydney Harbour at dusk" style="background:linear-gradient(180deg,#6d6fd0 0%,#c58bd0 40%,#e8b98c 70%,#2b3a5a 100%)"></div>
    <span class="card-edge left"></span><span class="card-edge right"></span>
    <div class="card-label"><p class="card-town">SYDNEY HARBOUR</p><p class="card-type">4 BEDROOM SIL HOME</p></div>
  </article>
  <article class="card" style="left:612px;top:1450px">
    <div class="card-photo" role="img" aria-label="St Mary's Cathedral and city skyline" style="background:linear-gradient(180deg,#3f8fd8 0%,#a9cde8 35%,#b99a6c 65%,#4f7a3a 100%)"></div>
    <span class="card-edge left"></span><span class="card-edge right"></span>
    <div class="card-label"><p class="card-town">ST MARY'S CATHEDRAL</p><p class="card-type">4 BEDROOM SIL HOME</p></div>
  </article>
</main>

<footer class="site-footer">
  <div class="footer-brand"><span class="brand-dot"></span><span class="brand-name">Tallowcrest Care</span></div>
  <ul class="contact-list">
    <li><svg width="14" height="11" viewBox="0 0 14 11"><rect x="0.75" y="0.75" width="12.5" height="9.5" fill="none" stroke="#e8477e" stroke-width="1.3"/><path d="M1 1l6 5 6-5" fill="none" stroke="#e8477e" stroke-width="1.3"/></svg>Email: info@tallowcrestcare.com.au</li>
    <li><svg width="14" height="14" viewBox="0 0 14 14"><path d="M3 1l2.5 3-1.5 1.5c1 2 2.5 3.5 4.5 4.5L10 8.5l3 2.5-1.5 2C6 12.5 1.5 8 1 2.5z" fill="#e8477e"/></svg>Phone: +61 0400 118 342</li>
    <li><svg width="14" height="14" viewBox="0 0 14 14"><circle cx="7" cy="7" r="6" fill="none" stroke="#e8477e" stroke-width="1.3"/><path d="M7 3.5V7l2.5 1.5" fill="none" stroke="#e8477e" stroke-width="1.3"/></svg>Operating Hours: 9AM To 5PM Monday - Friday</li>
  </ul>
  <div class="social" aria-label="Social links">
    <span class="badge"></span><span></span><span class="dark"></span><span></span>
  </div>
  <div class="footer-col" style="left:609px">
    <h3>ACCOMMODATION</h3>
    <ul>
      <li>Supported Independent Living (SIL)</li>
      <li>Specialist Disability<br>Accommodation (SDA)</li>
      <li>Short term Accommodation<br>(Respite)</li>
      <li>Vacancies</li>
    </ul>
  </div>
  <div class="footer-col" style="left:847px">
    <h3>WHAT WE DO</h3>
    <ul>
      <li>In Home Care</li>
      <li>Social &amp; Community Services</li>
      <li>Therapeutic Supports</li>
      <li>Support Coordination</li>
      <li>Home Modifications</li>
    </ul>
  </div>
</footer>
<div class="bottom-bar">© Copyright 2024 | Tallowcrest Care | All Rights Reserved.
  <span class="to-top"><svg width="10" height="7" viewBox="0 0 10 7"><path d="M0 7L5 1l5 6z" fill="#fff"/></svg></span>
</div>
</body>
</html>
```